New eyelid plastic surgery office needs a business card design-Eyelid Care Partners of the Brenton

I recently used PixelForge for my logo design and was very pleased with creativity and results. It was a difficult decision for me. Now I would like to create a business card based on this logo, which I will attach.

The text should be easily legible as some of my patients have difficulty seeing, but I would like a subtle, sophisticated artistry also evident to make the card memorable. Would like the card based on a similar color scheme as the logo but the inverse or other complementary colors may prove interesting
Updates

A good question was asked...my concern about my visually impaired patients was really my desire to avoid italicized or calligraphic type fonts that may be hard to read. Standard font size for a business card would be fine. Thanks!

Thank you so much for the great work so far. I wanted to give you my particular contact information to see if that would change the look of the cards. Martin Delacourt, MD Address: 2718 Harborview Lane, Suite 206 Wilmington, NC 28517 Phone: 910-555-0193 Fax: 910-555-0194 Website: www.brentonlidstudio.example Please delete the email slot from the card. Thanks so much!

Industry/Entity Type

Plastic

```html
<!DOCTYPE html>
<html lang="en">
<head>
<meta charset="utf-8">
<title>Eyelid Care Partners of the Brenton – Business Card</title>
<link rel="stylesheet" href="https://fonts.googleapis.com/css2?family=Marcellus&family=Tinos:wght@700&family=Arimo:wght@400;700&display=swap">
<style>
  :root {
    --page-bg: #2a1a14;
    --card-white: #ffffff;
    --card-edge: #a9c3dd;
    --brand-blue: #0f4c93;
    --ink: #111111;
    --band-navy: #0a1a6b;
    --band-royal: #1f2fd8;
    --band-deep: #0b158f;
    --band-steel: #3f78c4;
    --band-light: #8fb4dc;
    --ornament-gold: #c7a352;
  }
  * { margin: 0; padding: 0; box-sizing: border-box; }
  html, body { width: 1200px; height: 888px; overflow: hidden; }
  body {
    background: var(--page-bg);
    display: flex;
    align-items: center;
    justify-content: center;
  }
  .business-card {
    position: relative;
    width: 900px;
    height: 520px;
    background: radial-gradient(ellipse 70% 85% at 38% 55%, var(--card-white) 45%, var(--card-edge) 100%);
    overflow: hidden;
    box-shadow: 0 10px 30px rgba(0,0,0,.5);
  }
  .brand-name {
    position: absolute;
    left: 60px;
    top: 110px;
    width: 560px;
    font-family: "Marcellus", serif;
    color: var(--brand-blue);
    font-size: 44px;
    line-height: 1.1;
    letter-spacing: .5px;
  }
  .tagline {
    position: absolute;
    left: 60px;
    top: 250px;
    font-family: "Tinos", serif;
    font-weight: 700;
    font-size: 31px;
    color: var(--ink);
  }
  .contact {
    position: absolute;
    left: 40px;
    top: 340px;
    font-family: "Arimo", sans-serif;
    font-weight: 700;
    color: var(--ink);
  }
  .contact-head {
    display: flex;
    align-items: baseline;
    gap: 40px;
    margin-left: 20px;
  }
  .contact-label { font-size: 17px; }
  .doctor-name { font-size: 25px; }
  .contact-details {
    margin-top: 14px;
    border-left: 2px solid var(--ink);
    padding: 4px 0 4px 18px;
    display: grid;
    grid-template-columns: 80px auto;
    row-gap: 4px;
    font-size: 17px;
  }
  .band {
    position: absolute;
    top: 0;
    right: 0;
    width: 240px;
    height: 100%;
    display: flex;
  }
  .band-navy { width: 26px; background: var(--band-navy); }
  .band-ornaments {
    width: 150px;
    background: linear-gradient(90deg, var(--band-deep), var(--band-royal) 50%, var(--band-deep));
    position: relative;
  }
  .band-ornaments::after {
    content: "";
    position: absolute;
    inset: 0 22px;
    background: linear-gradient(180deg, rgba(199,163,82,.35), rgba(199,163,82,.2), rgba(199,163,82,.35));
  }
  .band-steel { width: 26px; background: var(--band-steel); }
  .band-light { flex: 1; background: linear-gradient(90deg, var(--band-steel), var(--band-light)); }
</style>
</head>
<body>
  <div class="business-card">
    <div class="brand-name">Eyelid Care Partners of the Brenton</div>
    <div class="tagline">New eyelid plastic surgery office</div>

    <div class="contact">
      <div class="contact-head">
        <span class="contact-label">Contact :</span>
        <span class="doctor-name">Martin Delacourt, MD</span>
      </div>
      <div class="contact-details">
        <span>Address</span><span>: 2718 Harborview Lane, Suite 206 Wilmington, NC 28517</span>
        <span>Phone</span><span>: 910 - 555 - 0193</span>
        <span>Fax</span><span>: 910 - 555 - 0194</span>
        <span>web</span><span>: www.brentonlidstudio.example</span>
      </div>
    </div>

    <div class="band">
      <div class="band-navy"></div>
      <div class="band-ornaments" role="img" aria-label="Column of gold filigree ornaments on royal blue"></div>
      <div class="band-steel"></div>
      <div class="band-light"></div>
    </div>
  </div>
</body>
</html>
```